AI Business Tools Landing Page

My web-based website builder (Pavlora.com) will be adding many new features in the very near future and I need an eye-catching landing page to promote these new products.

The page will have a primary section of the 8 main products we are promoting:
1. AI Instant Website Generator
2. AI Chatbot
3. Online Store Builder with AI Assistance
4. AI Auto-Blogging System
5. Online Scheduling System
6. Custom Email System
7. SEO Service
8. CRM System

The page will also have a smaller section for links to our affiliate programs. These can be smaller, less-promanent buttons or links. These are the affiliate products:
1. Get Your LLC
2. Website Design and Maintenance
3. Searchlane Ads Management
4. Social Media Posting Service
5. Logo Design
6. Trademark Registration
7. Patent Application
8. Printing Services (including postcards, flyers, and merch.)
9. Bulk AI Content Generator

The theme and color scheme of the page should follow the theme of our main website, which is https://pavlora.com.

I need the page fully coded and ready to deploy on my server.

I look forward to seeing your amazing designs!

```html
<!DOCTYPE html>
<html lang="en">
<head>
<meta charset="UTF-8">
<title>Pavlora – Additional Features &amp; Tools</title>
<link href="https://fonts.googleapis.com/css2?family=Poppins:wght@300;400;500;600;700&family=Outfit:wght@500;600&display=swap" rel="stylesheet">
<style>
  :root{
    --navy:#031333;
    --navy-deep:#020c22;
    --ink:#0b1530;
    --sky:#29c0f4;
    --sky-line:#47b6ec;
    --blue-btn:#27a6e6;
    --muted:#6b7488;
    --white:#ffffff;
  }
  *{box-sizing:border-box;margin:0;padding:0}
  html,body{width:716px;height:1200px;overflow:hidden;background:var(--white)}
  body{position:relative;font-family:"Poppins",sans-serif;color:var(--ink)}

  .hero{position:absolute;left:0;top:0;width:716px;height:385px;overflow:hidden;
    background:linear-gradient(90deg,#030f26 0%,#061c3d 45%,#0b3b66 75%,#0f4a78 100%)}
  .hero-visual{position:absolute;left:190px;top:0;width:526px;height:370px;
    background:radial-gradient(ellipse at 62% 42%,rgba(70,170,230,.55) 0%,rgba(30,110,170,.35) 30%,rgba(10,40,80,0) 70%)}
  .brand{position:absolute;display:flex;align-items:center;gap:7px;color:var(--white);font-weight:600}
  .brand-dot{width:20px;height:20px;border-radius:50%;background:var(--sky)}
  .brand--top{left:77px;top:15px;font-size:21px}
  .hero-title{position:absolute;left:75px;top:144px;color:var(--white);font-size:29px;line-height:33px}
  .hero-title strong{display:block;font-weight:700}
  .hero-title span{display:block;font-weight:300}
  .hero-wave{position:absolute;left:0;top:330px}
  .hero-pin{position:absolute;left:352px;top:330px;width:1.5px;height:52px;background:var(--sky-line)}
  .hero-pin::after{content:"";position:absolute;left:-2.5px;bottom:-4px;width:6px;height:6px;border-radius:50%;background:var(--sky-line)}

  .section-title{position:absolute;left:0;width:716px;text-align:center;font-weight:400;color:var(--ink)}
  .section-title b{font-weight:700}
  .features-title{top:407px;font-size:20px}
  .features-rule{position:absolute;left:333px;top:435px;width:45px;height:2px;background:var(--sky)}

  .feature{position:absolute;width:153px;border:1px solid #9fd8f3;border-radius:5px;background:var(--white);padding:0 10px}
  .feature--active{background:linear-gradient(160deg,#031333 0%,#062250 100%);border-color:#031333;color:var(--white)}
  .feature-icon{position:absolute;top:13px;left:20px}
  .feature h3{position:absolute;left:17px;right:6px;font-size:8px;font-weight:500;line-height:9.5px}
  .feature h3.nowrap{white-space:nowrap;font-size:7.6px}
  .feature ul{position:absolute;left:16px;right:5px;list-style:none}
  .feature li{font-size:6px;line-height:7.2px;padding-left:6px;position:relative;margin-bottom:7px}
  .feature li::before{content:"";position:absolute;left:0;top:2.5px;width:2.5px;height:2.5px;background:var(--sky)}

  .divider{position:absolute;left:42px;top:780px;width:633px;height:1px;background:#d7dbe2}
  .divider::after{content:"";position:absolute;left:316px;top:-2px;width:5px;height:5px;background:var(--sky)}
  .tools-title{top:803px;font-size:17.5px}

  .tool{position:absolute;width:199px;height:39px;border:1.5px solid #6cc6ef;border-radius:3px;
    display:flex;flex-direction:column;align-items:center;justify-content:center;
    font-family:"Outfit",sans-serif;font-weight:500;font-size:10.5px;color:var(--blue-btn)}
  .tool small{font-family:"Poppins",sans-serif;font-size:6px;color:var(--muted);font-weight:400;margin-top:1px}
  .tool--active{background:var(--navy);border-color:var(--navy);color:var(--white)}

  .footer{position:absolute;left:0;top:1030px;width:716px;height:170px}
  .brand--foot{left:66px;top:1100px;font-size:21px}
  .copyright{position:absolute;left:274px;top:1106px;font-size:9px;color:#d5dbe6;font-weight:300}
  .social{position:absolute;left:539px;top:1105px;display:grid;grid-template-columns:repeat(5,14px);column-gap:8px;row-gap:7px}
  .social span{width:14px;height:14px;border-radius:50%;background:var(--white)}
</style>
</head>
<body>

<header class="hero">
  <div class="hero-visual" role="img" aria-label="Robotic hand and human hand reaching toward a glowing digital network"></div>
  <div class="brand brand--top"><span class="brand-dot"></span>Pavlora</div>
  <h1 class="hero-title"><strong>Additional Features</strong><span>&amp; Tools for Website</span></h1>
  <svg class="hero-wave" width="716" height="60" viewBox="0 0 716 60">
    <path d="M0 28 C120 -8 260 10 360 22 C480 36 600 50 716 22 L716 60 L0 60Z" fill="var(--sky)"/>
    <path d="M0 50 C120 8 260 16 360 28 C480 40 600 56 716 36 L716 60 L0 60Z" fill="#fff"/>
  </svg>
  <div class="hero-pin"></div>
</header>

<h2 class="section-title features-title">Additional Features <b>for Your Website</b></h2>
<div class="features-rule"></div>

<!-- row 1 -->
<article class="feature" style="left:44px;top:467px;height:128px">
  <svg class="feature-icon" width="20" height="20" viewBox="0 0 20 20" fill="none" stroke="var(--sky)" stroke-width="1"><rect x="1" y="2" width="16" height="14" rx="1"/><line x1="1" y1="5" x2="17" y2="5"/><circle cx="15" cy="15" r="4" fill="#fff"/></svg>
  <h3 style="top:38px">AI Instant<br>Website Generator</h3>
  <ul style="top:63px">
    <li>Get a professional, SEO-optimized website in seconds!</li>
    <li>Includes custom domain, secure high-speed hosting, professional images, and more!</li>
  </ul>
</article>
<article class="feature feature--active" style="left:206px;top:467px;height:128px">
  <svg class="feature-icon" width="20" height="20" viewBox="0 0 20 20" fill="none" stroke="var(--sky)" stroke-width="1"><rect x="6" y="3" width="12" height="8" rx="3"/><rect x="1" y="9" width="10" height="7" rx="3"/></svg>
  <h3 style="top:38px;left:15px">AI ChatBot</h3>
  <ul style="top:55px;left:14px">
    <li>Fully-trainable ChatBot will learn about your business to automate the customer support process!</li>
    <li>Built-in CRM features integrate emailing, text messaging, and contact forms!</li>
  </ul>
</article>
<article class="feature" style="left:368px;top:467px;height:128px">
  <svg class="feature-icon" width="20" height="20" viewBox="0 0 20 20" fill="none" stroke="var(--sky)" stroke-width="1"><rect x="1" y="2" width="17" height="14" rx="1"/><path d="M5 8h9l-1 4H6z"/></svg>
  <h3 class="nowrap" style="top:37px;left:11px">Online Store Builder<br>(E-Commerce) with AI Assistance</h3>
  <ul style="top:63px;left:11px">
    <li>Sell you products online and integrate your products into any website!</li>
    <li>Accept payments from multiple payment gateways including Paystrand and Coinvale!</li>
  </ul>
</article>
<article class="feature" style="left:530px;top:467px;height:128px">
  <svg class="feature-icon" width="20" height="20" viewBox="0 0 20 20" fill="none" stroke="var(--sky)" stroke-width="1"><rect x="1" y="2" width="16" height="14" rx="1"/><line x1="1" y1="5" x2="17" y2="5"/><circle cx="15" cy="15" r="4" fill="#fff"/></svg>
  <h3 style="top:38px;left:13px">AI Auto-Blogging System</h3>
  <ul style="top:55px;left:13px">
    <li>AI will generate an incredible blog for your business in seconds and immediately begin posting content for you!</li>
    <li>Choose from daily, weekly, or monthly automated blog posting. Consistent, unique, SEO-optimized content posting on cruise control!</li>
  </ul>
</article>

<!-- row 2 -->
<article class="feature" style="left:44px;top:605px;height:141px">
  <svg class="feature-icon" width="22" height="22" viewBox="0 0 22 22" fill="none" stroke="var(--sky)" stroke-width="1" style="left:13px"><rect x="1" y="2" width="20" height="14" rx="1"/><line x1="7" y1="20" x2="15" y2="20"/><line x1="11" y1="16" x2="11" y2="20"/></svg>
  <h3 style="top:40px;left:15px">Online Scheduling<br>System</h3>
  <ul style="top:64px;left:15px">
    <li>Get appointment bookings, restaurant reservations, or consultations scheduled directly from your website!</li>
    <li>Manage your employees' schedules and all your appointments from a simple, user-friendly dashboard!</li>
  </ul>
</article>
<article class="feature" style="left:205px;top:605px;height:141px">
  <svg class="feature-icon" width="22" height="20" viewBox="0 0 22 20" fill="none" stroke="var(--sky)" stroke-width="1" style="left:13px"><rect x="1" y="1" width="20" height="17" rx="1"/><line x1="1" y1="5" x2="21" y2="5"/><line x1="5" y1="10" x2="17" y2="10"/><line x1="5" y1="13" x2="17" y2="13"/></svg>
  <h3 style="top:40px;left:13px">Custom emails using<br>your domain</h3>
  <ul style="top:64px;left:13px">
    <li>Quickly set up emails for yourself and all your employees with your own domain extension (example – johnd@yoursite.com). No more unprofessional Postly and Hollermail email addresses!</li>
    <li>Manage all your business emails from a simple, user-friendly interface!</li>
  </ul>
</article>
<article class="feature" style="left:368px;top:605px;height:141px">
  <svg class="feature-icon" width="22" height="22" viewBox="0 0 22 22" fill="none" stroke="var(--sky)" stroke-width="1" style="left:14px"><rect x="1" y="1" width="14" height="12" rx="1"/><rect x="6" y="8" width="14" height="12" rx="1" fill="#fff"/><path d="M10 16l5-5"/></svg>
  <h3 style="top:40px;left:15px">SEO Service – Automatic<br>Backlink Building</h3>
  <ul style="top:64px;left:15px">
    <li>Let us do the hard work of getting high-quality backlinks to your website. Although difficult to get, backlinks to your website boost search engine ranking more than any other strategy!</li>
    <li>Subscribe now and start getting 10-20 high-quality permanent backlinks to your website every month, guaranteed!</li>
  </ul>
</article>
<article class="feature" style="left:530px;top:605px;height:141px">
  <svg class="feature-icon" width="22" height="22" viewBox="0 0 22 22" fill="none" stroke="var(--sky)" stroke-width="1" style="left:12px"><circle cx="11" cy="9" r="8"/><circle cx="11" cy="8" r="3"/><rect x="3" y="14" width="16" height="7" rx="1" fill="#fff"/></svg>
  <h3 style="top:40px;left:13px">Customer Relationship<br>Management (CRM) System</h3>
  <ul style="top:66px;left:13px">
    <li>Automate the lead follow up process to consistently stay in front of your potential customers!</li>
    <li>Schedule automatic email and text campaigns and effortlessly follow your funnels from lead to closing!</li>
  </ul>
</article>

<div class="divider"></div>

<h2 class="section-title tools-title">More Tools to Help You <b>Grow Your Business</b></h2>

<a class="tool" style="left:59px;top:858px">Get Your LLC</a>
<a class="tool tool--active" style="left:266px;top:858px;width:198px">Social Media Posting Service</a>
<a class="tool" style="left:469px;top:858px">Patent Application</a>
<a class="tool" style="left:59px;top:905px">Website Design and Maintenance</a>
<a class="tool" style="left:266px;top:905px">Logo Design</a>
<a class="tool" style="left:469px;top:905px">Printing Services<small>(including postcards, flyers, and merch.)</small></a>
<a class="tool" style="left:59px;top:953px">Searchlane Ads Management</a>
<a class="tool" style="left:266px;top:953px">Trademark Registration</a>
<a class="tool" style="left:469px;top:953px">Bulk AI Content Generator</a>

<footer>
  <svg class="footer" viewBox="0 0 716 170" preserveAspectRatio="none">
    <path d="M0 10 C150 -6 300 20 420 40 C560 58 660 40 716 14 L716 170 L0 170Z" fill="var(--sky)"/>
    <path d="M0 20 C160 2 300 30 420 52 C560 72 660 50 716 24 L716 170 L0 170Z" fill="var(--navy)"/>
  </svg>
  <div class="brand brand--foot"><span class="brand-dot"></span>Pavlora</div>
  <p class="copyright">© 2024 Pavlora. All Rights Reserved</p>
  <div class="social" aria-label="Social links">
    <span></span><span></span><span></span><span></span><span></span>
    <span></span><span></span><span></span><span></span><span></span>
  </div>
</footer>

</body>
</html>
```